Single Webpage Custom Design

We need a single webpage design (no coding) that uses our color and design scheme (http://insight.veltomarsafe.com/).
We attached a draft that outlines the structure and content of what the page should look like.
As shown in the draft we need the following sections (in that order):
- Graphic with Text & Logo on top
- Product Explanation
- Customer Logos
- Success Stories with logo and citation each
- Contact form
- Footer

```html
<!DOCTYPE html>
<html lang="de">
<head>
<meta charset="utf-8">
<title>Veltora – Human Firewall</title>
<link href="https://fonts.googleapis.com/css2?family=Montserrat:wght@400;500;600;700;800&family=Open+Sans:wght@400;600;700&display=swap" rel="stylesheet">
<style>
:root{
  --teal:#1aaab5;
  --teal-dark:#1597a1;
  --teal-card:#1793a0;
  --teal-light:#aee0e4;
  --orange:#f6a623;
  --ink:#2d3436;
  --text:#5a6064;
  --muted:#8d9498;
  --line:#d6dadc;
  --grey-bg:#eceff0;
  --footer:#37474a;
  --white:#fff;
}
*{box-sizing:border-box;margin:0;padding:0}
html,body{width:1200px;height:4032px;overflow:hidden}
body{font-family:'Open Sans',sans-serif;color:var(--text);background:var(--white);position:relative}
h2.section-title{font-family:'Montserrat',sans-serif;font-weight:700;font-size:26px;color:var(--ink);text-align:center;text-transform:uppercase;position:absolute;left:0;width:100%}
.title-rule{position:absolute;left:50%;width:44px;height:3px;background:var(--orange);margin-left:-22px}
.on-teal{color:var(--white)!important}

/* HERO */
.hero{position:absolute;left:0;top:0;width:1200px;height:824px;background:linear-gradient(135deg,#1fb3bd 0%,#17a4b0 60%,#1aa9b3 100%);overflow:hidden}
.hero-photo{position:absolute;left:540px;top:110px;width:660px;height:618px;background:radial-gradient(ellipse at 55% 45%,#b0734f 0%,#7e6a5c 30%,#2d8f93 60%,rgba(26,170,181,0) 80%)}
.logo{position:absolute;left:116px;top:18px;display:flex;align-items:center;gap:8px}
.logo-mark{width:44px;height:44px;border-radius:50%;background:var(--orange)}
.logo-name{font-family:'Montserrat',sans-serif;font-weight:800;font-size:30px;color:#222}
.nav{position:absolute;top:30px;left:548px;display:flex}
.nav a{font-family:'Montserrat',sans-serif;font-size:13px;font-weight:500;color:var(--white);text-decoration:none;text-transform:uppercase;width:120px;text-align:center;position:relative}
.nav a.active::before{content:"";position:absolute;top:-30px;left:calc(50% - 24px);width:48px;height:3px;background:var(--orange)}
.hero h1{position:absolute;left:104px;top:206px;font-family:'Montserrat',sans-serif;font-weight:700;font-size:46px;color:var(--white);letter-spacing:.5px}
.hero-lead{position:absolute;left:104px;top:270px;width:720px;font-family:'Montserrat',sans-serif;font-size:20.5px;line-height:31px;color:var(--white)}
.checks{position:absolute;left:104px;top:348px;display:grid;grid-template-columns:250px 250px;row-gap:12px}
.checks li{list-style:none;display:flex;align-items:center;gap:9px;font-family:'Montserrat',sans-serif;font-weight:600;font-size:14px;color:var(--white)}
.chart{position:absolute;left:100px;top:440px}
.awards{position:absolute;left:0;top:728px;width:1200px;height:96px;background:rgba(255,255,255,.16);display:flex;padding-left:140px}
.award{display:flex;align-items:center;gap:14px;width:345px}
.award p{font-family:'Montserrat',sans-serif;font-weight:500;font-size:12px;line-height:17px;color:var(--white);width:200px}
.award-badge{width:42px;height:42px;border:2px solid var(--white);border-radius:50%;flex:none}

/* HOW */
.how{position:absolute;top:824px;left:0;width:1200px;height:470px;background:var(--white)}
.step{position:absolute;top:149px;width:325px;height:244px;border:1.5px solid var(--line)}
.step-tab{position:absolute;left:0;top:-11px;width:72px;height:71px;color:var(--white);font-family:'Montserrat',sans-serif;text-align:center;padding-top:14px;border-radius:4px 4px 0 0}
.step-tab small{display:block;font-size:13px;font-weight:500}
.step-tab b{display:block;font-size:19px;font-weight:700;line-height:22px}
.step h3{position:absolute;left:82px;top:14px;font-family:'Montserrat',sans-serif;font-weight:700;font-size:13px;line-height:17px;color:var(--teal);text-transform:uppercase}
.step .sub{position:absolute;left:82px;top:55px;width:225px;border-left:2px solid var(--teal);padding-left:8px;font-family:'Montserrat',sans-serif;font-weight:600;font-size:9.5px;line-height:13px;color:#333;text-transform:uppercase}
.step .body{position:absolute;left:82px;top:100px;width:230px;font-size:10px;line-height:16px;color:var(--muted)}
.step .item{position:absolute;left:82px;width:230px;display:flex;gap:12px;font-size:9px;line-height:13px;color:var(--muted)}
.step .item i{width:16px;height:16px;border:1.5px solid var(--muted);border-radius:3px;flex:none}

/* CUSTOM */
.custom{position:absolute;top:1294px;left:0;width:1200px;height:574px;background:var(--teal)}
.custom-intro{position:absolute;left:190px;top:128px;width:820px;text-align:center;font-family:'Montserrat',sans-serif;font-size:13px;line-height:23.5px;color:var(--white);text-transform:uppercase}
.feature{position:absolute;top:252px;height:226px;background:var(--white);border-radius:4px;box-shadow:0 4px 14px rgba(0,0,0,.12)}
.feature h3{font-family:'Montserrat',sans-serif;font-weight:700;font-size:18px;line-height:24px;color:var(--teal);text-transform:uppercase}
.feature p{font-size:11.5px;line-height:21px;color:var(--text);margin-top:14px}
.feature-img{position:absolute;border-radius:50% 45% 50% 40%}

/* CUSTOMERS */
.customers{position:absolute;top:1868px;left:0;width:1200px;height:501px;background:var(--white)}
.customers h2 em{font-style:normal;color:var(--orange)}
.client{position:absolute;display:flex;align-items:center;gap:8px;font-family:'Montserrat',sans-serif;font-weight:700;font-size:22px;color:#2c3e50;transform:translateX(-50%);white-space:nowrap}
.client i{width:22px;height:22px;background:#2c3e50;display:block}

/* STORIES */
.stories{position:absolute;top:2369px;left:0;width:1200px;height:517px;background:var(--teal)}
.story{position:absolute;top:153px;width:438px;height:247px;background:var(--teal-card)}
.story-brand{position:absolute;left:36px;top:34px;display:flex;align-items:center;gap:18px;font-family:'Montserrat',sans-serif;font-weight:700;font-size:30px;color:var(--white)}
.story-brand i{width:40px;height:40px;border:2px solid var(--white);border-radius:50%;display:block}
.story-brand i.sq{border-radius:4px;background:var(--white)}
.story blockquote{position:absolute;left:62px;top:98px;width:350px;font-family:'Montserrat',sans-serif;font-size:13.5px;line-height:23px;color:var(--white)}
.story blockquote::before{content:"\201C";position:absolute;left:-28px;top:-8px;font-size:40px;line-height:40px;font-weight:700;font-family:Georgia,serif}
.story blockquote::after{content:"\201D";font-size:40px;line-height:0;font-weight:700;font-family:Georgia,serif;vertical-align:-16px;margin-left:6px}
.btn-small{position:absolute;left:64px;top:179px;width:127px;height:34px;border-radius:17px;background:var(--orange);color:var(--white);font-family:'Montserrat',sans-serif;font-weight:600;font-size:12px;display:flex;align-items:center;justify-content:center;gap:6px}
.arrow{position:absolute;top:2606px}

/* CONTACT */
.contact{position:absolute;top:2886px;left:0;width:1200px;height:612px;background:var(--grey-bg)}
.field{position:absolute;height:55px;background:var(--white);border:2px solid #b9e3e7;font-family:'Montserrat',sans-serif;font-size:14px;color:#6b7175;padding:18px 22px}
.submit{position:absolute;left:513px;top:486px;width:189px;height:53px;border-radius:27px;background:var(--orange);color:var(--white);font-family:'Montserrat',sans-serif;font-weight:700;font-size:18px;display:flex;align-items:center;justify-content:center;gap:8px}

/* FOOTER */
.footer{position:absolute;top:3498px;left:0;width:1200px;height:467px;background:var(--footer);color:#e3e7e8}
.footer h4{position:absolute;font-family:'Montserrat',sans-serif;font-weight:700;font-size:14px;color:var(--white);text-transform:uppercase}
.footer .col{position:absolute;font-size:12px;line-height:21px}
.footer .col b{color:var(--white);font-weight:700}
.search{position:absolute;left:446px;top:108px;width:215px;height:32px;border:1px solid #c9d0d2;color:#c9d0d2;font-size:11px;padding:7px 12px}
.social li{list-style:none;display:flex;align-items:center;gap:12px;height:47.5px;font-size:13px}
.social i{width:31px;height:31px;border-radius:50%;background:var(--teal);display:block}
.info li{list-style:none;font-size:12px;line-height:30.2px}
.lang{position:absolute;left:939px;top:107px;width:143px;height:32px;border:1px solid #c9d0d2;font-size:11px;padding:7px 14px}
.foot-logo{position:absolute;left:942px;top:272px;display:flex;align-items:center;gap:8px}
.foot-logo .logo-name{color:var(--white)}
.copyright{position:absolute;top:3965px;left:0;width:1200px;height:67px;background:var(--teal);color:var(--white);font-size:12px;text-align:center;line-height:67px}
</style>
</head>
<body>

<header class="hero">
  <div class="hero-photo" role="img" aria-label="Woman with hands on hips wearing a brick-wall shirt and a cape, symbolising a human firewall"></div>
  <div class="logo"><span class="logo-mark"></span><span class="logo-name">Veltora</span></div>
  <nav class="nav">
    <a class="active">Home</a><a>Solution</a><a>Pricing</a><a>About</a><a>Contact</a>
  </nav>
  <h1>HUMAN FIREWALL</h1>
  <p class="hero-lead">Mittels Cyber Awareness Schulungen das Risiko von Attacken<br>innerhalb von 12 Monaten messbar um 50% senken</p>
  <ul class="checks">
    <li><svg width="21" height="21" viewBox="0 0 21 21"><circle cx="10.5" cy="10.5" r="10.5" fill="#fff"/><path d="M6 11l3 3 6-6" stroke="#1aaab5" stroke-width="2.4" fill="none"/></svg>Mit Geld Zuruck Garantie!</li>
    <li><svg width="21" height="21" viewBox="0 0 21 21"><circle cx="10.5" cy="10.5" r="10.5" fill="#fff"/><path d="M6 11l3 3 6-6" stroke="#1aaab5" stroke-width="2.4" fill="none"/></svg>Preiswerte Losung</li>
    <li><svg width="21" height="21" viewBox="0 0 21 21"><circle cx="10.5" cy="10.5" r="10.5" fill="#fff"/><path d="M6 11l3 3 6-6" stroke="#1aaab5" stroke-width="2.4" fill="none"/></svg>Individualisierbare Inhalte</li>
    <li><svg width="21" height="21" viewBox="0 0 21 21"><circle cx="10.5" cy="10.5" r="10.5" fill="#fff"/><path d="M6 11l3 3 6-6" stroke="#1aaab5" stroke-width="2.4" fill="none"/></svg>Datenschutzkonformk</li>
  </ul>
  <svg class="chart" width="440" height="260" viewBox="0 0 440 260" font-family="Montserrat, sans-serif" fill="#fff">
    <text x="6" y="22" font-size="12">Risk</text>
    <line x1="47" y1="8" x2="47" y2="226" stroke="#fff" stroke-width="2"/>
    <line x1="8" y1="224" x2="390" y2="224" stroke="#fff" stroke-width="2"/>
    <text x="398" y="226" font-size="12">Time</text>
    <rect x="67" y="21" width="42" height="100" fill="#f6a623"/><rect x="67" y="121" width="42" height="103" fill="#aee0e4"/>
    <rect x="146" y="75" width="42" height="72" fill="#f6a623"/><rect x="146" y="147" width="42" height="77" fill="#aee0e4"/>
    <rect x="225" y="128" width="42" height="32" fill="#f6a623"/><rect x="225" y="160" width="42" height="64" fill="#aee0e4"/>
    <rect x="295" y="165" width="42" height="59" fill="#aee0e4"/>
    <path d="M88 50 Q150 165 260 175 T380 188" stroke="#fff" stroke-width="2" fill="none"/>
    <g font-size="8.5" font-weight="700" text-anchor="middle">
      <text x="83" y="240">GENERIC</text><text x="83" y="250">TRAINING</text>
      <text x="170" y="237">ATTACK</text><text x="170" y="247">SIMULATION</text>
      <text x="246" y="240">SECURITY</text><text x="246" y="250">GAME</text>
      <text x="318" y="237">ROLE BASED</text><text x="318" y="247">TRAINING</text>
    </g>
  </svg>
  <div class="awards">
    <div class="award"><span class="award-badge"></span><p>In 2020, Veltora won the Security Excellence Award for Best Anti Phishing</p></div>
    <div class="award"><span class="award-badge"></span><p>In 2020, Veltora won the Security Excellence Award for the Best "Security Education Platform"</p></div>
    <div class="award"><span class="award-badge"></span><p>2020 Gold Winner "Cyber Security Education and Training" In the Secure Products Review</p></div>
  </div>
</header>

<section class="how">
  <h2 class="section-title" style="top:66px">How does it work?</h2>
  <span class="title-rule" style="top:103px"></span>

  <article class="step" style="left:97px">
    <div class="step-tab" style="background:#a7aaac"><small>STEP</small><b>No1</b></div>
    <h3>Set goals &amp;<br>create a plan</h3>
    <p class="sub">Understnding your goals will define program scope</p>
    <p class="body">Lorem Ipsum is simply dummy text of the printing and typesetting industry. Lorem Ipsum</p>
    <div class="item" style="top:145px"><i></i>Lorem Ipsum is simply dummy text of the printing and typesetting industry.</div>
    <div class="item" style="top:180px"><i></i>Lorem Ipsum is simply dummy text of the printing and typesetting industry.</div>
  </article>

  <article class="step" style="left:432px">
    <div class="step-tab" style="background:var(--orange)"><small>STEP</small><b>No2</b></div>
    <h3>Assess<br>awareness level</h3>
    <p class="sub">Use phishing simulations or assessments to undertand the current awareness level</p>
    <p class="body" style="top:112px">Lorem Ipsum is simply dummy text of the printing and typesetting industry. Lorem Ipsum</p>
    <div class="item" style="top:157px"><i style="border-color:var(--orange)"></i>Lorem Ipsum is simply dummy text of the printing and typesetting industry.</div>
    <div class="item" style="top:192px"><i style="border-color:var(--orange)"></i>Lorem Ipsum is simply dummy text of the printing and typesetting industry.</div>
  </article>

  <article class="step" style="left:768px">
    <div class="step-tab" style="background:var(--teal)"><small>STEP</small><b>No3</b></div>
    <h3>Run the awareness<br>campaign</h3>
    <p class="sub">Improve the security awareness level with tailored corses. Optimize the program over time</p>
    <p class="body" style="top:112px">Lorem Ipsum is simply dummy text of the printing and typesetting industry.</p>
    <div class="item" style="top:157px"><i style="border-color:var(--teal)"></i>Lorem Ipsum is simply dummy text of the printing and typesetting industry.</div>
    <div class="item" style="top:192px"><i style="border-color:var(--teal)"></i>Lorem Ipsum is simply dummy text of the printing and typesetting industry.</div>
  </article>
</section>

<section class="custom">
  <h2 class="section-title on-teal" style="top:66px">Fully customizable!</h2>
  <span class="title-rule" style="top:103px;background:#fff"></span>
  <p class="custom-intro">You might ask: why do the trainings need customization? In addition to adjusting the design (logo, font, colors) to your corporate look and feel, it is important that your emploees perceive the training as soemthing they can relate to. Examples:</p>

  <article class="feature" style="left:110px;width:469px">
    <div style="position:absolute;left:37px;top:45px;width:210px">
      <h3>From CEO:</h3>
      <p>Add a personal greeting message from your CEO at the start of the course to highlight the importance of the training.</p>
    </div>
    <div class="feature-img" role="img" aria-label="Laptop on a desk showing a video greeting from the CEO" style="left:250px;top:22px;width:200px;height:170px;background:linear-gradient(135deg,#7fd6dc 0%,#c9cfd2 55%,#5f6a70 100%)"></div>
  </article>

  <article class="feature" style="left:605px;width:476px">
    <div class="feature-img" role="img" aria-label="Screenshot of an internal policy document inside the training course" style="left:25px;top:30px;width:200px;height:170px;background:linear-gradient(160deg,#f4f6f7 0%,#e3e8ea 60%,#8fdbe0 100%)"></div>
    <div style="position:absolute;left:243px;top:45px;width:210px">
      <h3>Do you know our policies?</h3>
      <p>You could ask the user to read and acknowledge your internal policies prior to starting the course.</p>
    </div>
  </article>
</section>

<section class="customers">
  <h2 class="section-title" style="top:86px;font-size:22px">Mehr als <em>400</em> Kunden vertrauen bereits auf Veltora:</h2>
  <span class="title-rule" style="top:123px"></span>
  <div class="client" style="left:225px;top:200px">ALPENWERK</div>
  <div class="client" style="left:466px;top:200px;font-weight:600;font-size:20px">Kestrel Informatik</div>
  <div class="client" style="left:703px;top:200px;font-size:17px">Stadtwerk Nordhain<i></i></div>
  <div class="client" style="left:900px;top:200px">Railnet</div>
  <div class="client" style="left:1043px;top:200px"><i></i>Corvia</div>
  <div class="client" style="left:291px;top:327px">MAHLWERK</div>
  <div class="client" style="left:490px;top:327px">CHEMORA<i></i></div>
  <div class="client" style="left:704px;top:327px">Hausgarant</div>
  <div class="client" style="left:898px;top:327px;font-size:18px"><i style="border-radius:50%"></i>Tessmar</div>
</section>

<section class="stories">
  <h2 class="section-title on-teal" style="top:62px;font-size:28px">Success stories</h2>
  <svg class="arrow" style="left:76px" width="24" height="40" viewBox="0 0 24 40"><path d="M20 3L4 20l16 17" stroke="#fff" stroke-width="3.5" fill="none"/></svg>
  <svg class="arrow" style="left:1096px;top:2613px" width="24" height="40" viewBox="0 0 24 40"><path d="M4 3l16 17L4 37" stroke="#fff" stroke-width="3.5" fill="none"/></svg>

  <article class="story" style="left:147px">
    <div class="story-brand"><i></i>Aerovia</div>
    <blockquote>Veltora bietet ein optimales Gesamtpaket, mit<br>dem wir die Awareness bei unseren<br>Mitarbeitern dauehaft hochhalten konnen</blockquote>
    <span class="btn-small">Read More ›</span>
  </article>

  <article class="story" style="left:620px">
    <div class="story-brand"><i class="sq"></i>Polarkost</div>
    <blockquote style="left:68px">Es ist einfach ein tolles Gefuhl, wenn man<br>sieht, dass die Mitarbeiter deutlich<br>wachsamer geworden sind</blockquote>
    <span class="btn-small" style="left:55px">Read More ›</span>
  </article>
</section>

<section class="contact">
  <h2 class="section-title" style="top:70px;font-size:28px">Get in touch with us</h2>
  <span class="title-rule" style="top:110px"></span>
  <div class="field" style="left:131px;top:149px;width:465px">Full Name*</div>
  <div class="field" style="left:609px;top:149px;width:465px">Your Email*</div>
  <div class="field" style="left:131px;top:219px;width:465px">Phone</div>
  <div class="field" style="left:609px;top:219px;width:465px">Subject*</div>
  <div class="field" style="left:131px;top:287px;width:465px">Country</div>
  <div class="field" style="left:609px;top:287px;width:465px">Location</div>
  <div class="field" style="left:134px;top:354px;width:939px;height:114px">Message*</div>
  <div class="submit">Submit ›</div>
</section>

<footer class="footer">
  <h4 style="left:124px;top:72px">Contacts</h4>
  <div class="col" style="left:124px;top:105px">
    <b>Address: Europe</b><br>Veltora Security AG Brunnmattweg 12<br>6010 Kriens Switzerland<br><br>
    <b>Address: North America</b><br>Veltora Security USA 4410 Harbor Park Dr<br>Suite 210 Dayton, OH 45402<br><br>
    Phone Global: +41 44 555 01 27<br>Phone USA: +1-555-014-2231<br>Phone USA Support: +1-555-014-2290<br>Phone Canand: +1 555-017-3348<br>Phone France: +33 655 010 442<br>Phone UK: +44(0) 7700 900512
  </div>

  <h4 style="left:446px;top:74px">Search</h4>
  <div class="search">Search
    <svg style="position:absolute;right:8px;top:7px" width="16" height="16" viewBox="0 0 16 16"><circle cx="6.5" cy="6.5" r="5" stroke="#fff" stroke-width="2" fill="none"/><path d="M10 10l4.5 4.5" stroke="#fff" stroke-width="2"/></svg>
  </div>
  <h4 style="left:446px;top:176px">Connect</h4>
  <ul class="social col" style="left:446px;top:210px">
    <li><i></i>Friendloop</li>
    <li><i></i>Chirpline</li>
    <li><i></i>Vidstream</li>
    <li><i></i>Worknet</li>
  </ul>

  <h4 style="left:743px;top:76px">Infomation</h4>
  <ul class="info col" style="left:744px;top:108px">
    <li>Home</li><li>Solution</li><li>Pricing</li><li>Resources</li><li>About Us</li><li>Support Wiki</li><li>Contact</li><li>Download Veltora</li><li>Demo Request</li>
  </ul>

  <h4 style="left:936px;top:74px">Language</h4>
  <div class="lang">English
    <svg style="position:absolute;right:14px;top:13px" width="9" height="5" viewBox="0 0 9 5"><path d="M0 0h9L4.5 5z" fill="#fff"/></svg>
  </div>
  <div class="foot-logo"><span class="logo-mark"></span><span class="logo-name">Veltora</span></div>
</footer>
<div class="copyright">© Veltora All Rights Reserved 2021</div>

</body>
</html>
```